Quiet Harbor Podcast W/ Dr. Lena Marsh

Podcast Cover Art. I am in search of a re-design for my existing podcast. We have over 100 episodes, but I want to change the name to Quiet Harbor Podcast With Dr. Lena Marsh. I'm open to any ideas, and have attached source file image to use. ( note: NO brain images please).

```html
<!DOCTYPE html>
<html lang="en">
<head>
<meta charset="utf-8">
<title>Quiet Harbor Podcast With Dr. Lena Marsh</title>
<link rel="stylesheet" href="https://fonts.googleapis.com/css2?family=Poppins:wght@500;600;700&family=Allura&display=swap">
<style>
  :root {
    --coral: #ff6d55;
    --brown: #523610;
    --ink: #1f1a17;
    --sky-top: #eff0f2;
    --sky-mid: #e6eef1;
    --sky-bottom: #a9d3dc;
    --portrait-light: #f1d9cb;
    --portrait-warm: #f0a48f;
  }
  * { margin: 0; padding: 0; box-sizing: border-box; }
  html, body { width: 1200px; height: 1200px; overflow: hidden; }
  body { background: var(--sky-top); }
  .cover {
    position: relative;
    width: 1200px;
    height: 1200px;
    overflow: hidden;
    background: linear-gradient(180deg, var(--sky-top) 0%, var(--sky-top) 40%, var(--sky-mid) 70%, var(--sky-bottom) 100%);
    font-family: "Poppins", sans-serif;
  }
  .title {
    position: absolute;
    left: 80px;
    top: 38px;
    font-weight: 700;
    line-height: 1;
    letter-spacing: -2px;
  }
  .title-line-one {
    display: block;
    font-size: 268px;
    height: 240px;
  }
  .title-line-two {
    display: block;
    font-size: 176px;
    margin-top: 8px;
    color: var(--brown);
  }
  .accent { color: var(--coral); }
  .deep { color: var(--brown); }
  .with-script {
    position: absolute;
    left: 226px;
    top: 560px;
    font-family: "Allura", cursive;
    font-size: 104px;
    color: var(--ink);
    line-height: 1;
  }
  .host-name {
    position: absolute;
    left: 72px;
    top: 706px;
    font-size: 66px;
    font-weight: 600;
    color: var(--coral);
    letter-spacing: 0.5px;
    line-height: 1;
  }
  .show-label {
    position: absolute;
    left: 78px;
    top: 1082px;
    font-size: 46px;
    font-weight: 500;
    color: var(--brown);
    letter-spacing: 9px;
    line-height: 1;
  }
  .portrait {
    position: absolute;
    left: 650px;
    top: 470px;
    width: 550px;
    height: 730px;
  }
</style>
</head>
<body>
  <main class="cover">
    <h1 class="title">
      <span class="title-line-one"><span class="accent">QUI</span><span class="deep">ET</span></span>
      <span class="title-line-two">H<span class="accent">A</span>RBOR</span>
    </h1>

    <p class="with-script">with</p>
    <p class="host-name">DR. LENA MARSH</p>
    <p class="show-label">PODCAST</p>

    <svg class="portrait" viewBox="0 0 550 730" role="img" aria-label="Illustrated portrait of the host">
      <defs>
        <linearGradient id="portrait-fill" x1="0" y1="0" x2="0" y2="1">
          <stop offset="0" stop-color="var(--portrait-light)"/>
          <stop offset="1" stop-color="var(--portrait-warm)"/>
        </linearGradient>
      </defs>
      <path fill="url(#portrait-fill)" d="M40 0 H550 V730 H0 V40 A40 40 0 0 1 40 0 Z"/>
    </svg>
  </main>
</body>
</html>
```